Meadowrun Acres Website Design

We have been redeveloping our website already and are quite happy with the content, but the design needs to be better:
https://tilvexa-hub.examplehost.net/

Pages, content, concept etc. Can all be taken from the redeveloped website.
The farmer can register and edit/view their profile, subscribe and these pages need to be designed better as well as contact, about, pricing, tos, privacy and a page with example portlets.

We need a website to appeal to farmers, investors and retiring farmers.

The design should be clean and a little country.

We don't want any repeat designs that some may submit to every project and has no respect for the project brief, so please don't submit them.

Target Market(s)

farmers, investors, retirees

Industry/Entity Type

Farming

Number of Pages Required

5+ page

Colors

Designer to choose colors to be used in the design.

Requirements
Must have
• Nice, clean modern design that is appealing
• Profile page laid out nicely

```html
<!DOCTYPE html>
<html lang="en">
<head>
<meta charset="utf-8">
<title>Meadowrun Acres</title>
<link rel="stylesheet" href="https://fonts.googleapis.com/css2?family=Open+Sans:ital,wght@0,300;0,400;0,600;1,400&display=swap">
<style>
:root{
  --green:#3aa655;
  --green-dark:#2d6b3a;
  --green-deep:#1f6b2f;
  --text:#333;
  --muted:#9a9a9a;
  --white:#fff;
  --grey-band:#ececec;
  --font:"Open Sans",Arial,sans-serif;
}
*{box-sizing:border-box;margin:0;padding:0}
html,body{width:1200px;height:3614px;overflow:hidden}
body{font-family:var(--font);color:var(--text);background:var(--white);position:relative}
.section{position:absolute;left:0;width:1200px}
.media{position:absolute;display:block}
.btn-outline{position:absolute;border:2px solid var(--white);color:var(--white);font-size:15px;text-align:center;text-transform:uppercase;letter-spacing:.5px}

/* hero */
.hero{top:0;height:650px}
.hero .media{inset:0;background:linear-gradient(135deg,#6f6a5e 0%,#8a7a66 35%,#5d6a4c 65%,#7e8a6a 100%)}
.hero .shade{position:absolute;inset:0;background:rgba(0,0,0,.22)}
.brand{position:absolute;left:130px;top:38px;display:flex;align-items:center;gap:12px;color:var(--white);font-size:24px;font-weight:400}
.brand-dot{width:36px;height:36px;border-radius:50%;border:2px solid var(--white)}
.nav{position:absolute;left:462px;top:48px;display:flex;gap:0}
.nav a{color:var(--white);text-decoration:none;font-size:16px;margin-right:27px}
.login{position:absolute;left:962px;top:0;width:124px;height:34px;background:var(--green);color:var(--white);font-size:15px;text-align:center;line-height:32px;border-radius:0 0 14px 14px}
.hero h1{position:absolute;top:252px;width:100%;text-align:center;color:var(--white);font-size:56px;font-weight:400;letter-spacing:1px}
.hero .sub{position:absolute;top:322px;width:100%;text-align:center;color:var(--white);font-size:28px;letter-spacing:1px}
.hero .btn-outline{left:513px;top:376px;width:170px;height:46px;line-height:42px;font-size:14px}
.dots{position:absolute;top:612px;left:562px;display:flex;gap:8px}
.dots span{width:14px;height:14px;border-radius:50%;background:var(--white)}
.dots span.active{background:transparent;border:2px solid var(--white)}

/* intro */
.intro{top:650px;height:445px}
.intro h2{position:absolute;top:64px;width:100%;text-align:center;font-size:30px;font-weight:400;color:#333}
.intro p{position:absolute;top:115px;left:220px;width:760px;text-align:center;font-size:16px;color:var(--muted);line-height:26px}
.tiles{position:absolute;top:175px;left:130px;display:flex;gap:8px}
.tile{position:relative;width:228px;height:212px;color:var(--white);font-size:15px;display:flex;align-items:center;justify-content:center;text-align:center;line-height:20px}
.tile .media{inset:0}
.tile span{position:relative;padding:0 24px}
.t1 .media{background:linear-gradient(160deg,#7b6e5b,#3f4b32)}
.t2 .media{background:linear-gradient(160deg,#5a4a3e,#a48366)}
.t3 .media{background:linear-gradient(160deg,#8d9aa4,#3c3a30)}
.t4 .media{background:linear-gradient(160deg,#d8c68a,#5e6b3d)}

/* aspiring */
.aspiring{top:1095px;height:430px}
.aspiring .media{inset:0;background:linear-gradient(180deg,#3f5a78 0%,#54657a 40%,#3e5a38 75%,#2d4a2a 100%)}
.aspiring h2{position:absolute;top:30px;width:100%;text-align:center;color:var(--white);font-size:30px;font-weight:400}
.step{position:absolute;top:88px;width:304px;height:304px;border-radius:50%;border:8px solid rgba(255,255,255,.55);display:flex;flex-direction:column;align-items:center;text-align:center;padding-top:70px}
.step h3{font-size:20px;font-weight:600;margin-top:12px}
.step p{font-size:15px;line-height:22px;margin-top:4px;width:220px}
.step.light{background:var(--white);color:var(--green)}
.step.light p{color:var(--muted)}
.step.dark{background:var(--green);color:var(--white)}
.step.deep{background:var(--green-deep);color:var(--white)}

/* pricing */
.pricing{top:1525px;height:435px}
.pricing .media{left:0;top:0;width:600px;height:435px;background:linear-gradient(150deg,#8a6a50 0%,#6a4a34 45%,#c8b8a2 100%)}
.pricing .panel{position:absolute;left:600px;top:0;width:600px;height:435px;background:var(--green);color:var(--white)}
.pricing h2{position:absolute;left:72px;top:82px;font-size:28px;font-weight:400}
.pricing p{position:absolute;left:72px;width:420px;font-size:13.5px;line-height:22px}
.pricing .p1{top:132px}
.pricing .p2{top:200px}
.pricing .btn-outline{left:72px;top:298px;width:142px;height:38px;line-height:34px;text-transform:none}

/* videos */
.videos{top:1960px;height:455px}
.videos h2{position:absolute;top:52px;width:100%;text-align:center;font-size:32px;font-weight:400;color:var(--green-dark)}
.video{position:absolute;top:120px;width:448px;height:272px}
.video .media{inset:0}
.v1{left:150px}
.v1 .media{background:linear-gradient(120deg,#c9b48e,#7a6048 60%,#4a3a2c)}
.v2{left:634px}
.v2 .media{background:linear-gradient(120deg,#2f3f6a,#4e5e84 55%,#7a6a58)}
.play{position:absolute;left:184px;top:96px}
.controls{position:absolute;left:0;bottom:0;width:100%;height:22px;background:rgba(0,0,0,.55);color:#ddd;font-size:10px;line-height:22px;padding-left:10px}

/* testimonials */
.testimonials{top:2415px;height:425px;background:var(--grey-band)}
.testimonials h2{position:absolute;top:52px;width:100%;text-align:center;font-size:28px;font-weight:400}
.quote-card{position:absolute;left:302px;top:155px;width:604px;height:186px;background:var(--white);box-shadow:0 4px 14px rgba(0,0,0,.18);text-align:center}
.quote-badge{position:absolute;left:265px;top:-38px;width:76px;height:76px;border-radius:50%;background:var(--white);display:flex;align-items:center;justify-content:center}
.quote-badge span{width:34px;height:34px;border-radius:50%;border:2px solid var(--green)}
.quote-card blockquote{position:absolute;left:70px;top:52px;width:464px;font-size:13px;font-style:italic;line-height:23px;color:var(--muted)}
.quote-mark{position:absolute;top:40px;font-size:42px;color:var(--green);font-weight:600;line-height:1}
.quote-mark.open{left:42px}
.quote-mark.close{right:42px}
.quote-card cite{position:absolute;top:136px;width:100%;font-style:normal;font-size:15px;font-weight:600;color:var(--green)}
.arrow{position:absolute;top:185px}

/* retiring */
.retiring{top:2840px;height:410px}
.retiring .media{inset:0;background:linear-gradient(180deg,#3e4a3a 0%,#5a6a48 45%,#6a6438 80%,#4a4a2e 100%)}
.retiring .shade{position:absolute;inset:0;background:rgba(0,0,0,.3)}
.retiring h2{position:absolute;top:95px;width:100%;text-align:center;color:var(--white);font-size:30px;font-weight:400}
.retiring p{position:absolute;top:150px;left:205px;width:790px;text-align:center;color:var(--white);font-size:15px;line-height:26px}
.retiring .btn-outline{left:523px;top:253px;width:154px;height:38px;line-height:34px;text-transform:none}

/* footer */
.footer{top:3250px;height:364px;background:var(--green-dark);color:var(--white)}
.col{position:absolute;top:58px}
.col h4{font-size:18px;font-weight:400;margin-bottom:16px}
.col li{list-style:none;font-size:13px;line-height:28px}
.col.links{left:133px}
.col.support{left:348px}
.col.contact{left:585px}
.contact-row{display:flex;align-items:flex-start;gap:10px;font-size:13px;line-height:26px}
.contact-row svg{margin-top:6px;flex:none}
.social{display:flex;gap:8px;margin-top:14px;padding-left:2px}
.social span{width:28px;height:28px;border-radius:50%;background:rgba(255,255,255,.85)}
.footer-brand{position:absolute;left:866px;top:58px;width:190px;text-align:center;color:rgba(255,255,255,.8);font-size:22px}
.footer-brand .mark{width:92px;height:92px;border-radius:50%;border:3px solid rgba(255,255,255,.8);margin:0 auto 18px}
.footer .rule{position:absolute;left:133px;top:290px;width:934px;height:1px;background:rgba(255,255,255,.2)}
.copyright{position:absolute;top:313px;width:100%;text-align:center;font-size:11px;color:rgba(255,255,255,.75)}
</style>
</head>
<body>

<header class="section hero">
  <div class="media" role="img" aria-label="Farmer family with children and a dog sitting outside a farm shed"></div>
  <div class="shade"></div>
  <div class="brand"><span class="brand-dot"></span>Meadowrun Acres</div>
  <nav class="nav">
    <a href="#">Home</a><a href="#">Aspiring Farmers</a><a href="#">Investors</a><a href="#">Retiring Farmer</a><a href="#">Blog</a><a href="#">Pricing</a>
  </nav>
  <div class="login">Log In</div>
  <h1>ASPIRING FARMERS</h1>
  <div class="sub">ETIAM EU URNA SED PORTA SUSPENDISSE QUAM</div>
  <div class="btn-outline">Enquire now</div>
  <div class="dots"><span class="active"></span><span></span><span></span><span></span></div>
</header>

<section class="section intro">
  <h2>You Can Own A Farm</h2>
  <p>We know how hard it is for a young family to find the capital required to own and operate their own farm - so we started Meadowrun Acres.</p>
  <div class="tiles">
    <div class="tile t1"><div class="media" role="img" aria-label="Young farming family outdoors"></div><span>We connect a young farming family</span></div>
    <div class="tile t2"><div class="media" role="img" aria-label="Retiring farmers together"></div><span>With a retiring farming family</span></div>
    <div class="tile t3"><div class="media" role="img" aria-label="Open farm shed under the sky"></div><span>And investors</span></div>
    <div class="tile t4"><div class="media" role="img" aria-label="Cattle grazing in a sunlit paddock"></div><span>To own and operate a farm together</span></div>
  </div>
</section>

<section class="section aspiring">
  <div class="media" role="img" aria-label="Green crop rows with hills and a cloudy sky"></div>
  <h2>Aspiring Farmers</h2>
  <div class="step light" style="left:130px">
    <svg width="70" height="52" viewBox="0 0 70 52" fill="none" stroke="currentColor" stroke-width="2.5">
      <circle cx="16" cy="10" r="7"/><circle cx="54" cy="10" r="7"/><circle cx="35" cy="20" r="6"/>
      <path d="M6 50V28a10 10 0 0 1 20 0v22M44 50V28a10 10 0 0 1 20 0v22M27 50V36a8 8 0 0 1 16 0v14"/>
    </svg>
    <h3>Step 1</h3>
    <p>Register as an Aspiring Farmer</p>
  </div>
  <div class="step dark" style="left:448px">
    <svg width="86" height="58" viewBox="0 0 86 58" fill="none" stroke="currentColor" stroke-width="2.5">
      <path d="M20 30V8h26l6 22M46 8v22M10 30h66v10H10z"/>
      <circle cx="24" cy="44" r="12"/><circle cx="66" cy="48" r="8"/><path d="M66 30V14"/>
    </svg>
    <h3>Step 2</h3>
    <p>Build your farm skills to get yourself farm-ready.</p>
  </div>
  <div class="step deep" style="left:766px">
    <svg width="40" height="64" viewBox="0 0 40 64" fill="none" stroke="currentColor" stroke-width="2.5">
      <path d="M6 62L34 4M22 30c-8-2-12-8-12-16 8 2 12 8 12 16zM26 22c6-4 12-4 14 0-4 6-10 6-14 0zM16 42c-8-2-12-8-12-14 8 2 12 8 12 14zM20 34c6-4 12-4 14 0-4 6-10 6-14 0z"/>
    </svg>
    <h3>Step 3</h3>
    <p>Together we find you your dream farm.</p>
  </div>
</section>

<section class="section pricing">
  <div class="media" role="img" aria-label="Inside a wooden shearing shed with a child standing"></div>
  <div class="panel">
    <h2>Our Pricing</h2>
    <p class="p1">enim iaculis aliquam Mauris nunc quam venenatis nec euismod sit amet egestas placerat est Pellentesque habitant morbi tristique senectus et</p>
    <p class="p2">netus et malesuada fames ac turpis egestas Cras id elit Integer quis urna Ut ante enim</p>
    <div class="btn-outline">Click here</div>
  </div>
</section>

<section class="section videos">
  <h2>Watch Our Videos</h2>
  <div class="video v1">
    <div class="media" role="img" aria-label="Video still of a young farmer speaking indoors"></div>
    <svg class="play" width="80" height="80" viewBox="0 0 80 80"><circle cx="40" cy="40" r="36" fill="rgba(0,0,0,.15)" stroke="#fff" stroke-width="3"/><path d="M32 26l22 14-22 14z" fill="none" stroke="#fff" stroke-width="3"/></svg>
    <div class="controls">0:01 / 2:15</div>
  </div>
  <div class="video v2">
    <div class="media" role="img" aria-label="Video still of a man speaking beside farm machinery"></div>
    <svg class="play" width="80" height="80" viewBox="0 0 80 80"><circle cx="40" cy="40" r="36" fill="rgba(0,0,0,.15)" stroke="#fff" stroke-width="3"/><path d="M32 26l22 14-22 14z" fill="none" stroke="#fff" stroke-width="3"/></svg>
  </div>
</section>

<section class="section testimonials">
  <h2>Testimonials</h2>
  <svg class="arrow" style="left:222px" width="26" height="60" viewBox="0 0 26 60"><path d="M24 2L2 30l22 28" fill="none" stroke="#bbb" stroke-width="2"/></svg>
  <svg class="arrow" style="left:952px" width="26" height="60" viewBox="0 0 26 60"><path d="M2 2l22 28L2 58" fill="none" stroke="#bbb" stroke-width="2"/></svg>
  <div class="quote-card">
    <div class="quote-badge"><span></span></div>
    <div class="quote-mark open">&ldquo;</div>
    <div class="quote-mark close">&rdquo;</div>
    <blockquote>Land access is a major barrier to growing more farmers, and we are really excited to see the development of things like Meadowrun Acres - creative ways to assist young or emerging farmers onto land!</blockquote>
    <cite>By Author Name</cite>
  </div>
</section>

<section class="section retiring">
  <div class="media" role="img" aria-label="Farmers on horseback with cattle in an evening paddock"></div>
  <div class="shade"></div>
  <h2>Retiring Farmers</h2>
  <p>Are you looking for a positive way to step back from your farm? We can connect you with a passionate aspiring farming family who will love your farm just as much as you do. No registration required and your information will be kept private Get in touch discuss the best farm succession opportunity for you</p>
  <div class="btn-outline">Click here</div>
</section>

<footer class="section footer">
  <div class="col links">
    <h4>Quick Links</h4>
    <ul><li>Farmers</li><li>Investors</li><li>Retiring</li><li>About</li><li>Pricing</li></ul>
  </div>
  <div class="col support">
    <h4>Support</h4>
    <ul><li>Contact</li><li>Terms of Service</li><li>Privacy</li><li>Newsletter</li></ul>
  </div>
  <div class="col contact">
    <h4>Contact Info</h4>
    <div class="contact-row">
      <svg width="14" height="18" viewBox="0 0 14 18"><path d="M7 0a7 7 0 0 0-7 7c0 5 7 11 7 11s7-6 7-11a7 7 0 0 0-7-7zm0 10a3 3 0 1 1 0-6 3 3 0 0 1 0 6z" fill="#fff"/></svg>
      <span>410 Willowbend Road Suite 12<br>Brookfield, OR 97100</span>
    </div>
    <div class="contact-row">
      <svg width="16" height="16" viewBox="0 0 16 16"><path d="M3 1l3 3-2 2c1 2 4 5 6 6l2-2 3 3-2 2C7 15 1 9 1 3z" fill="none" stroke="#fff" stroke-width="1.5"/></svg>
      <span>(555) 018-4420</span>
    </div>
    <div class="contact-row">
      <svg width="16" height="12" viewBox="0 0 16 12"><rect x="1" y="1" width="14" height="10" fill="none" stroke="#fff" stroke-width="1.5"/><path d="M1 1l7 6 7-6" fill="none" stroke="#fff" stroke-width="1.5"/></svg>
      <span>hello@meadowrunacres.example</span>
    </div>
    <div class="social"><span></span><span></span><span></span><span></span></div>
  </div>
  <div class="footer-brand"><div class="mark"></div>Meadowrun Acres</div>
  <div class="rule"></div>
  <div class="copyright">&copy; 2017 Company Name. All right reserved. Term of Use</div>
</footer>

</body>
</html>
```